Revamp Of Landing Page For an Automated AI Voice Agents Agency

here is my current landing page https://app.brightfernpromotionhub.biz/v2/preview/WXKRPmQ4hLzYBvNdTeGS?notrack=true

Please use all my current content and imagery of ai agents in your new design. Make it easy to ready, easy to navigate and easy to understand

I am looking for a SLEEK shiny polished looking website. I like Dark themed sites but am open to see light themed sites too so please dont be shy.

The site should have an Ai Voice Agent Theme about it. Maybe look and feel of futureistic but simple and not intimidating to the average person...

Here are a couple website designs I like for reference:
https://q7v.io/
https://ai-bots.marekholvin.com/
https://chatwelmo.com/ai-agents

Target Market(s)

b2b

Industry/Entity Type

AI Voice Agents

Coding

Coded - Design and coding required

Font styles to use
Other font styles liked:
• open

Requirements
Must have
• all elements and content and images used in existing design.
Nice to have
• open
Should not have
• open

```html
<!DOCTYPE html>
<html lang="en">
<head>
<meta charset="utf-8">
<title>Voxora — Ai Voice Agents</title>
<link href="https://fonts.googleapis.com/css2?family=Outfit:wght@500;600;700&family=Poppins:wght@400;500;600&display=swap" rel="stylesheet">
<style>
:root{
  --bg:#0c0520;
  --bg-deep:#07031a;
  --panel:#150a33;
  --panel-edge:#3a2470;
  --violet:#8b5cf6;
  --violet-strong:#6d28d9;
  --magenta:#c026d3;
  --orange:#f0642a;
  --gold:#f6a21e;
  --text:#ffffff;
  --muted:#c9c2e0;
  --link:#e14cc8;
}
*{margin:0;padding:0;box-sizing:border-box}
html,body{width:1200px;height:4669px;overflow:hidden}
body{background:var(--bg);color:var(--text);font-family:"Poppins",sans-serif;position:relative}
.abs{position:absolute}
h1,h2,h3,.brand{font-family:"Outfit",sans-serif}
.btn{position:absolute;display:flex;align-items:center;justify-content:center;color:#fff;font-size:13px;font-weight:500;text-decoration:none;background:linear-gradient(90deg,var(--violet-strong),var(--violet))}
.btn.round{border-radius:24px;font-size:15px}
.btn.magenta{background:linear-gradient(90deg,#8a1fc8,var(--magenta))}
.link{color:var(--link);text-decoration:underline}
.glow{text-shadow:0 0 14px rgba(139,92,246,.9),0 0 4px rgba(168,120,255,.8)}
.brand{font-weight:600;letter-spacing:2px;display:flex;align-items:center;gap:10px;color:#fff}
.brand .dot{width:16px;height:16px;border-radius:50%;background:var(--violet)}

/* hero */
.hero{left:0;top:0;width:1200px;height:650px;background:radial-gradient(circle at 85% 60%,#1b4a55 0%,#14123a 35%,#120a30 70%);overflow:hidden}
.hero .art{left:648px;top:-10px;width:560px;height:570px;border-radius:50%;background:radial-gradient(circle at 55% 50%,#3fd3c3 0%,#1b7c84 40%,#0f3a4a 75%);box-shadow:0 0 0 2px rgba(246,162,30,.5)}
.hero h1{left:85px;top:134px;font-size:48px;font-weight:600;color:var(--violet)}
.hero .sub{left:85px;top:197px;width:540px;font-size:31px;line-height:41px;font-weight:400}
.hero .small{left:85px;top:382px;width:540px;font-size:12.5px;line-height:23px;font-weight:500}

/* workforce */
.work{left:0;top:650px;width:1200px;height:1000px;background:linear-gradient(180deg,#10062b,#0d0524)}
.work h2{left:141px;top:25px;font-size:34px;line-height:38px;font-weight:700;text-transform:uppercase}
.work .lead{left:141px;top:260px;width:255px;font-size:12px;line-height:19px;color:var(--muted)}
.card{position:absolute;width:290px;height:437px;border:1px solid var(--panel-edge);background:linear-gradient(180deg,#130a30,#1f0a45);text-align:center}
.card .photo{position:absolute;left:8px;top:8px;width:274px;height:176px}
.card .badge{position:absolute;left:117px;top:156px;width:56px;height:56px;border-radius:50%;border:3px solid #fff;display:flex;align-items:center;justify-content:center}
.card h3{position:absolute;left:0;width:100%;top:224px;font-family:"Poppins",sans-serif;font-size:15px;font-weight:500}
.card p{position:absolute;left:18px;width:254px;top:257px;font-size:11.3px;line-height:18px;color:var(--muted)}
.card p b{color:#fff;font-weight:600;display:block}

/* wish */
.wish{left:0;top:1650px;width:1200px;height:450px;background:radial-gradient(ellipse at 50% 75%,#2c1aa0 0%,#1a0e5c 35%,#0c0520 70%);text-align:center}
.wish .label{top:118px;width:100%;color:var(--orange);font-size:14px;font-weight:500;letter-spacing:1px}
.wish h2{top:146px;width:100%;font-size:32px;font-weight:700}
.wish .p1{top:210px;width:100%;font-size:15px;font-weight:500}
.wish .p2{top:240px;left:265px;width:670px;font-size:15px;line-height:23px;font-weight:500}

/* never sick */
.sick{left:0;top:2100px;width:1200px;height:380px;background:linear-gradient(180deg,#0c0520,#160a38)}
.sick h2{top:28px;width:100%;text-align:center;font-size:32px;font-weight:700}
.feat{position:absolute;top:98px;width:240px;text-align:center}
.feat .ico{width:88px;height:88px;border-radius:50%;margin:0 auto;display:flex;align-items:center;justify-content:center}
.feat h3{font-family:"Poppins",sans-serif;font-size:14px;font-weight:500;margin-top:30px;letter-spacing:.5px}
.feat p{font-size:11.5px;line-height:17px;color:var(--muted);margin-top:12px}

/* hired */
.hired{left:0;top:2480px;width:1200px;height:540px;background:linear-gradient(180deg,#160a38,#0d0524)}
.hired .bolt{left:743px;top:22px;width:345px;height:435px;background:radial-gradient(ellipse at 50% 50%,#ff7a2a 0%,#a63a5a 35%,#2a1050 70%,transparent 75%)}
.hired h2{left:141px;top:65px;font-size:32px;line-height:38px;font-weight:700}
.hired .label{left:141px;top:169px;color:var(--orange);font-size:14px;font-weight:600;letter-spacing:.5px}
.hired .tag{left:141px;top:198px;width:420px;font-size:20px;line-height:28px;font-weight:500}
.hired .lead{left:141px;top:333px;width:360px;font-size:12px;line-height:19px;color:var(--muted)}

/* promise */
.promise{left:0;top:3020px;width:1200px;height:450px;background:var(--bg)}
.stars-card{position:absolute;left:141px;top:57px;width:290px;height:348px;border:1px solid var(--panel-edge);background:linear-gradient(180deg,#1a0b3a,#0f0628);text-align:center}
.stars-card h3{margin-top:42px;font-size:24px;line-height:32px;font-weight:600;text-transform:uppercase}
.stars-card .stars{display:flex;justify-content:center;gap:8px;margin-top:10px}
.promise h2{left:455px;top:60px;width:604px;text-align:center;font-size:32px;font-weight:700}
.pcard{position:absolute;top:151px;width:290px;height:254px;border:1px solid var(--panel-edge);text-align:center}
.pcard .ico{width:86px;height:86px;border-radius:50%;margin:36px auto 0;display:flex;align-items:center;justify-content:center;border:3px solid #fff}
.pcard h3{font-family:"Poppins",sans-serif;font-size:15px;line-height:19px;font-weight:500;margin-top:26px;text-transform:uppercase}
.pcard p{font-size:11.5px;line-height:18px;color:var(--muted);margin-top:12px}

/* faq */
.faq{left:0;top:3470px;width:1200px;height:500px;background:var(--bg)}
.faq h2{top:82px;width:100%;text-align:center;font-size:32px;font-weight:700}
.q{position:absolute;left:263px;width:674px;height:40px;background:#2a2446;display:flex;align-items:center;padding-left:52px;font-size:15px;font-weight:500}
.q::before{content:"";position:absolute;left:10px;top:8px;width:24px;height:24px;border-radius:50%;border:3px solid var(--violet)}
.a{position:absolute;left:314px;width:600px;font-size:11.5px;line-height:22px;color:var(--muted)}
.rail{position:absolute;left:285px;width:1px;background:#3b3558}

/* closing */
.close{left:0;top:3970px;width:1200px;height:699px;background:linear-gradient(180deg,#0c0520,#140833)}
.close h2{top:97px;width:100%;text-align:center;font-size:34px;line-height:38px;font-weight:700}
.close .lead{top:277px;left:330px;width:540px;text-align:center;font-size:12px;line-height:19px;color:var(--muted)}
.close .brand{left:0;width:100%;justify-content:center;top:426px;font-size:38px}
.legal{left:141px;width:918px;font-size:11px;color:var(--muted)}
.refund{left:141px;top:553px;width:918px;height:32px;background:var(--magenta);display:flex;align-items:center;justify-content:center;font-size:11px;color:#fff}
</style>
</head>
<body>

<section class="hero abs">
  <div class="art abs" role="img" aria-label="White AI robot assistant sitting with a laptop on a teal glowing background"></div>
  <div class="brand abs" style="left:85px;top:30px;font-size:30px"><span>VOXORA</span><span class="dot"></span></div>
  <h1 class="abs">Ai Voice Agents</h1>
  <p class="sub abs">That Answer Calls, Book Appts, Send Emails, Text Messages, Follow Up Reminders, Transfer Calls &amp; More For You 24x7!</p>
  <p class="small abs">We Will Create An Ai Agent Customized For Your Business At No Cost. Simply Click The Button Below And Your Very Own Ai Agent Will Be Calling You In Just A Couple Minutes. Experience The Magic And Get Ready To Be Very Impressed!</p>
  <a class="btn round" href="#" style="left:85px;top:491px;width:238px;height:44px">Get An Instant Free Demo</a>
</section>

<section class="work abs">
  <h2 class="abs glow">Meet Your<br>New AI-<br>Powered<br>Workforce</h2>
  <a class="btn" href="#" style="left:141px;top:200px;width:201px;height:34px">Get An Instant Free Demo</a>
  <p class="lead abs">We Will Create An Ai Agent Customized For Your Business At No Cost. Simply <span class="link">Click The Button</span> Above And Your Very Own Ai Agent Will Be Calling You In Just A Couple Minutes. Experience The Magic And Get Ready To Be Very Impressed!</p>

  <div class="card" style="left:453px;top:21px">
    <div class="photo" role="img" aria-label="Sales agent with headset working at a desk by a city window" style="background:linear-gradient(160deg,#c9ccd4,#5a5f6e)"></div>
    <div class="badge" style="background:#6d28d9"><svg width="26" height="26" viewBox="0 0 24 24" fill="none" stroke="#fff" stroke-width="2"><circle cx="12" cy="10" r="5"/><path d="M4 21c1-4 4-6 8-6s7 2 8 6"/></svg></div>
    <h3>Ai Sales Agent</h3>
    <p>Brian will take your inbound sales calls. Will give all detailed information to the customer, answer questions in a normal conversational tone and can book sales appointments or transfer hot prospects to a human to close the sale.</p>
  </div>
  <div class="card" style="left:769px;top:21px">
    <div class="photo" role="img" aria-label="Receptionist with headset in a purple lit office" style="background:linear-gradient(160deg,#6a7ad8,#a04ab8)"></div>
    <div class="badge" style="background:#c026d3"><svg width="26" height="26" viewBox="0 0 24 24" fill="none" stroke="#fff" stroke-width="2"><path d="M4 5h16v10H9l-5 4z"/></svg></div>
    <h3>Ai Receptionist</h3>
    <p><b>Takes Overflow and After Hours Calls or Can Take Calls 24/7 &amp; Transfer To Appropriate Dept.</b>Cody handles all your calls 24/7. You can also set him to only take overflow calls and after hours. He can send emails and sms messages and even book appointments over the call</p>
  </div>
  <div class="card" style="left:141px;top:485px;background:linear-gradient(180deg,#0e1a24,#0b2a22)">
    <div class="photo" role="img" aria-label="Robot assistant with headset booking appointments at a computer" style="background:linear-gradient(160deg,#b9bfc7,#4a5058)"></div>
    <div class="badge" style="background:#16a34a"><svg width="26" height="26" viewBox="0 0 24 24" fill="none" stroke="#fff" stroke-width="2"><rect x="4" y="6" width="16" height="14"/><path d="M4 10h16M8 3v5M16 3v5"/></svg></div>
    <h3>Ai Appointment Setter</h3>
    <p><b>Book Appts &amp; Reservations On Auto Pilot</b>Bobby offers business advice, helps brainstorm ideas, and provides insights on growth tactics to support your entrepreneurial journey.</p>
  </div>
  <div class="card" style="left:453px;top:485px;background:linear-gradient(180deg,#0d1430,#0c1a46)">
    <div class="photo" role="img" aria-label="Agents with headsets at computers in a blue lit office" style="background:linear-gradient(160deg,#24406e,#0f1a30)"></div>
    <div class="badge" style="background:#2563eb"><svg width="26" height="26" viewBox="0 0 24 24" fill="none" stroke="#fff" stroke-width="2"><path d="M3 5h18l-7 8v6l-4-2v-4z"/></svg></div>
    <h3>Ai Lead Qualifier</h3>
    <p><b>Conversate With Prospects To Qualify Before Handing Over To Sales Team</b>All of our ai agents gather information and qualify leads. If they are interested in the services on the call then our ai agents will assist them with booking an appointment with our sales team over the call.</p>
  </div>
  <div class="card" style="left:769px;top:485px;background:linear-gradient(180deg,#1a1220,#2a1a10)">
    <div class="photo" role="img" aria-label="Humanoid robot assistant in a bright office" style="background:linear-gradient(160deg,#c4c9cf,#6b7078)"></div>
    <div class="badge" style="background:#f59e0b"><svg width="26" height="26" viewBox="0 0 24 24" fill="none" stroke="#fff" stroke-width="2"><path d="M6 16V11a6 6 0 0 1 12 0v5l2 2H4z"/><path d="M10 21h4"/></svg></div>
    <h3>Ai Follow Up Reminders</h3>
    <p><b>Calls, Sends SMS &amp; Email Reminders</b>Sam handles all the follow up calls, appt reminders and sends out the email and sms reminders too.</p>
  </div>
</section>

<section class="wish abs">
  <p class="label abs">INSTALL THE POWER OF AI FOR YOUR BUSINESS</p>
  <h2 class="abs glow">YOUR WISH IS THEIR COMMAND</h2>
  <p class="p1 abs">Your New Ai Agents Will Never Call In Sick And Will Never Complain!</p>
  <p class="p2 abs">With your new team of AI Agents, handling inbound calls, sending emails and sms messages, booking appointments and handling customer service inquiries is going to save you a ton of time and money.</p>
</section>

<section class="sick abs">
  <h2 class="abs glow">AN EMPLOYEE THAT NEVER GETS SICK!</h2>
  <div class="feat" style="left:224px">
    <div class="ico" style="background:radial-gradient(circle,#0f3a22,#081a12);box-shadow:0 0 0 3px #16a34a"><svg width="40" height="40" viewBox="0 0 24 24" fill="none" stroke="#fff" stroke-width="1.6"><rect x="6" y="6" width="12" height="12" rx="2"/><path d="M9 2v4M15 2v4M9 18v4M15 18v4M2 9h4M2 15h4M18 9h4M18 15h4"/></svg></div>
    <h3>TRAINED IN SECONDS</h3><p>Learns Your Entire Website<br>In Seconds</p>
  </div>
  <div class="feat" style="left:480px">
    <div class="ico" style="background:radial-gradient(circle,#3a1040,#1a0820);box-shadow:0 0 0 3px #c026d3"><svg width="40" height="40" viewBox="0 0 24 24" fill="none" stroke="#fff" stroke-width="1.6"><circle cx="12" cy="12" r="9"/><path d="M3 12h18M12 3c3 3 3 15 0 18M12 3c-3 3-3 15 0 18"/></svg></div>
    <h3>WORLDWIDE</h3><p>Works Anywhere In<br>The Globe</p>
  </div>
  <div class="feat" style="left:732px">
    <div class="ico" style="background:radial-gradient(circle,#3a220a,#1a1006);box-shadow:0 0 0 3px #f59e0b"><svg width="40" height="40" viewBox="0 0 24 24" fill="none" stroke="#fff" stroke-width="1.6"><circle cx="12" cy="8" r="4"/><path d="M4 21c1-5 4-7 8-7s7 2 8 7"/></svg></div>
    <h3>USER-FRIENDLY</h3><p>Your Ai Agents Sound As If<br>They're Real Humans</p>
  </div>
</section>

<section class="hired abs">
  <div class="bolt abs" role="img" aria-label="Glowing orange lightning bolt with the words lightning responses"></div>
  <h2 class="abs glow">OUR AI AGENTS<br>OUR READY TO BE HIRED</h2>
  <p class="label abs">LIGHTNING-FAST RESPONSES</p>
  <p class="tag abs">Instant answers, no coffee, bathroom or lunch breaks needed</p>
  <a class="btn" href="#" style="left:141px;top:276px;width:201px;height:34px">Get An Instant Free Demo</a>
  <p class="lead abs">We Will Create An Ai Agent Customized For Your Business At No Cost. Simply <span class="link">Click The Button</span> Above And Your Very Own Ai Agent Will Be Calling You In Just A Couple Minutes. Experience The Magic And Get Ready To Be Very Impressed!</p>
</section>

<section class="promise abs">
  <div class="stars-card">
    <h3>After our<br>customers have<br>a conversation<br>with their new<br>AI voice agent<br>they give us 5<br>stars!</h3>
    <div class="stars">
      <svg width="28" height="28" viewBox="0 0 24 24"><path fill="#f97316" d="M12 2l3 7 7 .6-5.3 4.6 1.6 7.3L12 17.8 5.7 21.5l1.6-7.3L2 9.6 9 9z"/></svg>
      <svg width="28" height="28" viewBox="0 0 24 24"><path fill="#f97316" d="M12 2l3 7 7 .6-5.3 4.6 1.6 7.3L12 17.8 5.7 21.5l1.6-7.3L2 9.6 9 9z"/></svg>
      <svg width="28" height="28" viewBox="0 0 24 24"><path fill="#f97316" d="M12 2l3 7 7 .6-5.3 4.6 1.6 7.3L12 17.8 5.7 21.5l1.6-7.3L2 9.6 9 9z"/></svg>
      <svg width="28" height="28" viewBox="0 0 24 24"><path fill="#f97316" d="M12 2l3 7 7 .6-5.3 4.6 1.6 7.3L12 17.8 5.7 21.5l1.6-7.3L2 9.6 9 9z"/></svg>
      <svg width="28" height="28" viewBox="0 0 24 24"><path fill="#f97316" d="M12 2l3 7 7 .6-5.3 4.6 1.6 7.3L12 17.8 5.7 21.5l1.6-7.3L2 9.6 9 9z"/></svg>
    </div>
  </div>
  <h2 class="abs glow">OUR PROMISE TO YOU:</h2>
  <div class="pcard" style="left:455px;background:radial-gradient(ellipse at 50% 30%,#0f4a22,#081a10 75%)">
    <div class="ico" style="background:#16a34a"><svg width="40" height="40" viewBox="0 0 24 24" fill="none" stroke="#fff" stroke-width="1.6"><rect x="4" y="6" width="16" height="14"/><path d="M4 10h16M8 3v5M16 3v5"/><text x="12" y="18" font-size="6" fill="#fff" stroke="none" text-anchor="middle">14</text></svg></div>
    <h3>14-Day Money-Back<br>Guarantee*</h3>
  </div>
  <div class="pcard" style="left:769px;background:radial-gradient(ellipse at 50% 30%,#1a2a8a,#0a0f3a 75%)">
    <div class="ico" style="background:#2563eb"><svg width="40" height="40" viewBox="0 0 24 24" fill="none" stroke="#fff" stroke-width="1.6"><circle cx="12" cy="12" r="9"/><text x="12" y="15" font-size="7" fill="#fff" stroke="none" text-anchor="middle">24</text></svg></div>
    <h3>24/7 Customer<br>Support</h3>
    <p>Often praised for our friendly<br>&amp; helpful support team</p>
  </div>
</section>

<section class="faq abs">
  <h2 class="abs glow">DO YOU HAVE QUESTIONS?</h2>
  <div class="rail" style="top:196px;height:290px"></div>
  <div class="q" style="top:156px">What exactly are the AI Voice Agents?</div>
  <p class="a" style="top:208px">AI Voice Agents are specialized human sounding bots, having smart and masterful conversations and each is expertly trained in seconds for a specific business function.</p>
  <div class="q" style="top:273px">How will these AI Voice Agents benefit</div>
  <p class="a" style="top:325px">Ai Voice Agents Answer Calls, Book Appts, Send Emails, Text Messages, Follow Up Reminders &amp; More For You 24/7!</p>
  <div class="q" style="top:390px">Are they easy to use?</div>
  <p class="a" style="top:442px">We provide a done for you service. We create your AI Voice Agent and launch it within days!</p>
</section>

<section class="close abs">
  <h2 class="abs glow">THESE AI AGENTS CAN HELP<br>YOUR BUSINESS TREMENDOUSLY.<br>IMAGINE THE POSSIBILITIES</h2>
  <a class="btn magenta" href="#" style="left:499px;top:226px;width:202px;height:34px">Get An Instant Free Demo</a>
  <p class="lead abs">We Will Create An Ai Agent Customized For Your Business At No Cost. Simply <span class="link">Click The Button</span> Above And Your Very Own Ai Agent Will Be Calling You In Just A Couple Minutes. Experience The Magic And Get Ready To Be Very Impressed!</p>
  <div class="brand abs"><span>VOXORA</span><span class="dot" style="width:22px;height:22px"></span></div>
  <div class="legal abs" style="top:512px;display:flex;justify-content:space-between;border-top:1px solid #2a2248;padding-top:0">
    <span>© 2025 Voxora. All rights reserved.</span>
    <span>Disclaimer: Privacy | Terms &amp; Conditions | Earnings &amp; Products Disclaimer</span>
  </div>
  <div class="refund abs">*14-Day Money Back Guarantee Terms: If you use the ai agents and you're not happy. Then you can contact us in the first 14 days for a full refund.</div>
  <p class="legal abs" style="top:604px;text-align:center">Do you have questions about ( ) Please email ( )</p>
  <p class="legal abs" style="top:653px;text-align:center;line-height:18px">IMPORTANT: This site is not a part of the Friendnet website or Friendnet Inc. Additionally,<br>this site is NOT endorsed by Friendnet in any way. FRIENDNET is a trademark of FRIENDNET, Inc.</p>
</section>

</body>
</html>
```